Birchline Septic Solutions

Would like to see some single sided ones but would also like to see some double sided with one sided only being the logo. Owners name is Colin Vandro. Phone number is 555-214-0387
Services are pumping, inspections, installs, and repairs

Contact Information for Business Card

555-241-0387 Colin Vandro Alderbrook, OH

```html
<!DOCTYPE html>
<html lang="en">
<head>
<meta charset="utf-8">
<title>Birchline Septic Solutions – Business Card</title>
<link href="https://fonts.googleapis.com/css2?family=Montserrat:wght@500;600;800&display=swap" rel="stylesheet">
<style>
  :root {
    --ink: #0a0a0a;
    --paper: #ffffff;
    --teal: #2bbdb8;
    --backdrop: #c9c9c9;
    --card-w: 545px;
    --card-h: 312px;
  }
  * { box-sizing: border-box; margin: 0; padding: 0; }
  html, body {
    width: 1200px; height: 800px; overflow: hidden;
    background: var(--backdrop);
    font-family: "Montserrat", sans-serif;
  }
  .sheet {
    width: 1200px; height: 800px;
    display: flex; align-items: center; justify-content: center; gap: 40px;
  }
  .card {
    position: relative;
    width: var(--card-w); height: var(--card-h);
    border-radius: 18px; overflow: hidden;
    box-shadow: 0 0 0 2px var(--teal), 0 14px 30px rgba(0,0,0,.25);
  }
  .card-bg { position: absolute; inset: 0; }

  /* Front: contact side */
  .front .wordmark {
    position: absolute; left: 36px; top: 118px; width: 210px;
    color: var(--ink); font-weight: 800; font-size: 25px;
    line-height: 1.15; text-transform: uppercase; letter-spacing: .04em;
  }
  .front .owner-name {
    position: absolute; right: 34px; top: 58px;
    color: var(--paper); font-weight: 800; font-size: 23px;
    letter-spacing: .02em; text-transform: uppercase;
  }
  .contact-list {
    position: absolute; right: 24px; top: 132px;
    list-style: none; display: flex; flex-direction: column; gap: 18px;
  }
  .contact-item {
    display: flex; align-items: center; justify-content: flex-end; gap: 12px;
    color: var(--paper); font-weight: 500; font-size: 17px; letter-spacing: .03em;
  }
  .contact-icon { width: 24px; height: 24px; flex: none; }

  /* Back: brand side */
  .back { background: var(--ink); }
  .back .wordmark {
    position: absolute; left: 0; right: 0; top: 92px;
    text-align: center; color: var(--paper);
    font-weight: 800; font-size: 34px; line-height: 1.15;
    text-transform: uppercase; letter-spacing: .06em;
  }
  .services {
    position: absolute; left: 0; right: 0; bottom: 40px;
    text-align: center; color: var(--teal);
    font-weight: 600; font-size: 15.5px; letter-spacing: .05em;
    text-transform: uppercase;
  }
  .services .dot { color: var(--paper); margin: 0 6px; }
</style>
</head>
<body>
<main class="sheet">

  <section class="card front" aria-label="Business card, contact side">
    <svg class="card-bg" viewBox="0 0 545 312" aria-hidden="true">
      <rect width="545" height="312" fill="var(--paper)"/>
      <polygon points="250,0 545,0 545,312 300,312" fill="var(--ink)"/>
      <polygon points="268,48 545,48 545,88 256,88" fill="var(--teal)"/>
    </svg>
    <p class="wordmark">Birchline Septic Solutions</p>
    <h1 class="owner-name">Colin Vandro</h1>
    <ul class="contact-list">
      <li class="contact-item">
        <span>555-214-0387</span>
        <svg class="contact-icon" viewBox="0 0 24 24" aria-hidden="true">
          <circle cx="12" cy="12" r="12" fill="var(--teal)"/>
          <path d="M8 7.5c.6-.6 1.3-.5 1.7.1l1 1.6c.3.5.2 1-.2 1.4l-.7.6c.6 1.2 1.6 2.2 2.8 2.8l.6-.7c.4-.4.9-.5 1.4-.2l1.6 1c.6.4.7 1.1.1 1.7l-.8.8c-.7.7-2 .8-3.6-.1-1.6-.9-3.2-2.5-4.1-4.1-.9-1.6-.8-2.9-.1-3.6z" fill="var(--ink)"/>
        </svg>
      </li>
      <li class="contact-item">
        <span>Alderbrook, OH</span>
        <svg class="contact-icon" viewBox="0 0 24 24" aria-hidden="true">
          <circle cx="12" cy="12" r="12" fill="var(--teal)"/>
          <path d="M12 5.5a4.3 4.3 0 0 0-4.3 4.3c0 3.2 4.3 8.2 4.3 8.2s4.3-5 4.3-8.2A4.3 4.3 0 0 0 12 5.5z" fill="var(--ink)"/>
          <circle cx="12" cy="9.8" r="1.6" fill="var(--teal)"/>
        </svg>
      </li>
    </ul>
  </section>

  <section class="card back" aria-label="Business card, brand side">
    <p class="wordmark">Birchline<br>Septic Solutions</p>
    <p class="services">
      Pumping<span class="dot">•</span>Inspections<span class="dot">•</span>Installs<span class="dot">•</span>Repairs
    </p>
  </section>

</main>
</body>
</html>
```